Computer Company needs a Business card design

We need a business card design for our business. We assist people to transition to the KVS (Kestrel Vantage Scheme). The Verandal Crown Office-owned kvs™ network is a brand new telecommunications network currently being rolled out across Australia, giving access to a reliable broadband connection. Our niche market will predominantly be domestic customers in the 50+ age bracket. The assistance that we provide is everything from arranging the equipment, arranging the plan and contract term, appointment times, final testing of the network and any tweaks that need to be made. We basically PM the transition from start to finish. The business card design should be minimalist, should communicate loyalty and stability, should be easy to read and clearly explain what we do. We have asked for front and back. However, the back of the card does not have to include much information at all. It could be just a small design, or a repeat of our phone number. Up to you. The attached file only says what is required on the card. It does not specify where to arrange the text, what fonts to use, etc etc. As much as we would like to give you more info, due to our very limited design ability, we are not really able to send you any rough, or otherwise, designs of what we are after. Hopefully the above description is enough for you.

```html
<!DOCTYPE html>
<html lang="en">
<head>
<meta charset="utf-8">
<title>Linkwise Home – Business Card</title>
<link rel="stylesheet" href="https://fonts.googleapis.com/css2?family=Mulish:wght@400;700;800&display=swap">
<style>
  :root {
    --backdrop: #c9c9c9;
    --card-blue: #0a86af;
    --card-white: #f4f4f4;
    --ink-white: #ffffff;
    --brand-blue: #0b83ab;
    --accent-orange: #f0840f;
    --card-shadow: rgba(0, 0, 0, 0.28);
  }
  * { box-sizing: border-box; margin: 0; padding: 0; }
  html, body {
    width: 1200px;
    height: 960px;
    overflow: hidden;
    background: var(--backdrop);
    font-family: "Mulish", "Century Gothic", sans-serif;
  }
  .stage {
    position: relative;
    width: 1200px;
    height: 960px;
  }
  .card {
    position: absolute;
    left: 320px;
    width: 600px;
    height: 340px;
    box-shadow: 0 3px 6px var(--card-shadow);
  }
  .card--front {
    top: 108px;
    background: var(--card-blue);
    color: var(--ink-white);
    text-align: center;
  }
  .contact {
    position: absolute;
    top: 114px;
    left: 0;
    right: 0;
  }
  .contact__name {
    font-size: 21px;
    font-weight: 700;
    letter-spacing: 0.8px;
    line-height: 26px;
  }
  .contact__role {
    font-size: 15px;
    letter-spacing: 0.5px;
    line-height: 20px;
  }
  .contact__details {
    margin-top: 10px;
    list-style: none;
    font-size: 14px;
    line-height: 19px;
    letter-spacing: 0.3px;
  }
  .card--back {
    top: 493px;
    background: var(--card-white);
    display: flex;
    align-items: center;
    justify-content: center;
  }
  .brand {
    display: flex;
    align-items: center;
    gap: 16px;
    margin-top: 10px;
  }
  .brand__dot {
    width: 30px;
    height: 30px;
    border-radius: 50%;
    background: var(--accent-orange);
  }
  .brand__name {
    font-size: 50px;
    font-weight: 800;
    color: var(--brand-blue);
    letter-spacing: 0.5px;
    line-height: 1;
  }
</style>
</head>
<body>
  <main class="stage">
    <section class="card card--front" aria-label="Card front">
      <div class="contact">
        <h1 class="contact__name">ROSS PENFIELD</h1>
        <p class="contact__role">CEO/FOUNDER</p>
        <ul class="contact__details">
          <li>0491578320</li>
          <li>ross@linkwisehome.com.au</li>
          <li>www.linkwisehome.com.au</li>
        </ul>
      </div>
    </section>
    <section class="card card--back" aria-label="Card back">
      <div class="brand">
        <span class="brand__dot" aria-hidden="true"></span>
        <p class="brand__name">Linkwise Home</p>
      </div>
    </section>
  </main>
</body>
</html>
```